Psychology service brochure

Marketing brochure for a new psychological counselling service.
Our old brochure was too boring and conservative. We are selling our services to GP's, psychiatrists, other health providers and of course potential clients. We'd really like a professional, elegant look that conveys us to be compassionate and conscientious providers of psychological services.
I have included a copy of our old brochure and a copy of the changes we'd like to the text.
Updates
I have included a photo of myself and my business partner. Only the faces are needed, so backgrounds would need to be edited out.
Hello, in consultation with my business partner, we would like
the use of our photos in the brochure please (with backgrounds edited out)
no stock photos of random people
use of abstract or nature/floral motifs suggestive of tranquillity
regards,
Rosalind
Target Market(s)
General practitioner doctors, potential clients
Industry/Entity Type
Health
Requirements
Must have
- must include BlairMdITC TT- font for the business name
- must include our signature color Pantone 291 (see attached brochure)
- use of the photos of myself and my business partner (with background edited out please)
- keep use of colours to a minimum, 3 colors maximum, one of which must be Pantone 291
- must include changes to the brochure as outlined in the 'Changes to Pamphlet' document.
Nice to have
- an interesting, eye catching layout.
- interesting use of white spaces
- use of subtle abstract or nature/floral related graphics suggestive of tranquillity
Should not have
- should not include our fee
- stock photos of people

```html
<!DOCTYPE html>
<html lang="en">
<head>
<meta charset="utf-8">
<title>Quiet Harbour Counselling – Brochure</title>
<link rel="stylesheet" href="https://fonts.googleapis.com/css2?family=Arimo:wght@400;700&display=swap">
<style>
  :root {
    --sky: #b3f2f9;
    --sky-soft: #d4f8fc;
    --sky-deep: #9fe9f3;
    --forest: #1c6a2b;
    --paper: #ffffff;
    --backdrop: #ffffff;
  }
  * { box-sizing: border-box; margin: 0; padding: 0; }
  html, body {
    width: 1200px; height: 900px; overflow: hidden;
    background: var(--backdrop);
    font-family: "Arimo", Arial, sans-serif;
  }
  .brochure {
    position: absolute; left: 106px; top: 94px;
    width: 998px; height: 711px;
    background: var(--paper);
    box-shadow: 3px 5px 8px rgba(0,0,0,0.35);
  }
  .edge-band {
    position: absolute; left: 0; top: 0; width: 20px; height: 100%;
    background: var(--sky);
  }
  .section-heading {
    position: absolute; left: 20px; width: 250px; height: 54px;
    background: var(--sky);
    color: var(--paper);
    font-weight: 700; font-size: 16px; line-height: 20px;
    letter-spacing: 0.9px; text-transform: uppercase;
    padding: 11px 0 0 36px;
  }
  .section-heading::after {
    content: ""; position: absolute; left: 250px; bottom: 0;
    width: 60px; height: 4px; background: var(--sky);
  }
  .heading-approach { top: 52px; }
  .heading-clients { top: 368px; }
  .approach-copy {
    position: absolute; left: 56px; top: 127px; width: 220px;
    color: var(--forest); font-size: 12.4px; line-height: 14px;
  }
  .approach-copy p { margin-bottom: 6px; }
  .client-goals {
    position: absolute; left: 57px; top: 438px; width: 215px;
    list-style: none;
    color: var(--forest); font-size: 12.4px; line-height: 14px;
  }
  .client-goals li { position: relative; padding-left: 12px; margin-bottom: 7px; }
  .client-goals li::before {
    content: ""; position: absolute; left: 0; top: 5px;
    width: 5px; height: 5px; border-radius: 50%; background: var(--forest);
  }
  .location-map {
    position: absolute; left: 357px; top: 108px; width: 274px; height: 276px;
    border: 1px solid var(--sky); border-radius: 12px;
    background: linear-gradient(160deg, #f4fdfe, var(--sky-soft));
    box-shadow: 3px 4px 4px rgba(179,242,249,0.7);
  }
  .contact-panel {
    position: absolute; left: 330px; top: 461px; width: 328px; height: 165px;
    background: var(--sky);
    color: var(--paper); font-size: 12.4px; line-height: 20.5px;
    padding-top: 23px;
  }
  .contact-panel .line { text-align: center; }
  .contact-panel .centre-name { font-weight: 700; letter-spacing: 0.4px; }
  .contact-row { display: flex; }
  .contact-row .label { width: 107px; text-align: right; padding-right: 8px; }
  .contact-row .value { font-weight: 700; }
  .sky-panel {
    position: absolute; left: 658px; top: 0; width: 259px; height: 100%;
    background:
      radial-gradient(ellipse 90px 60px at 190px 200px, rgba(255,255,255,0.7), transparent),
      radial-gradient(ellipse 110px 140px at 70px 530px, rgba(255,255,255,0.75), transparent),
      radial-gradient(ellipse 70px 50px at 60px 80px, rgba(255,255,255,0.5), transparent),
      linear-gradient(180deg, var(--sky), var(--sky-deep) 60%, var(--sky));
  }
  .brand-name {
    position: absolute; left: 950px; top: 670px;
    transform-origin: 0 0; transform: rotate(-90deg);
    width: 630px; white-space: nowrap;
    color: var(--sky); font-size: 27px; letter-spacing: 3.6px;
    text-transform: uppercase; line-height: 30px;
  }
</style>
</head>
<body>
<main class="brochure">
  <div class="edge-band"></div>

  <h2 class="section-heading heading-approach">Our approach<br>to therapy</h2>
  <div class="approach-copy">
    <p>We are warm, compassionate and professional Clinical General Psychologists who together have thirty years of experience and who are committed to providing high quality evidence-based treatment to our clients.</p>
    <p>Types of treatment may include Cognitive Behavioural Therapy, Motivational Interviewing and Mindfulness.</p>
    <p>We also eligible to provide Pregnancy Support Counselling services under Medicare.</p>
  </div>

  <h2 class="section-heading heading-clients">What we want<br>for our clients</h2>
  <ul class="client-goals">
    <li>For you to feel heard and respected</li>
    <li>To have a positive experience of working collaboratively with a psychologist</li>
    <li>To connect or reconnect with feelings of hope</li>
    <li>To move beyond counselling with an understanding of your strengths and the skills to make changes that will help you to meet future challenges.</li>
  </ul>

  <div class="location-map" role="img" aria-label="Street map showing the centre's location near the train station"></div>

  <address class="contact-panel" style="font-style:normal">
    <div class="line">Contact reception</div>
    <div class="line centre-name">THE ELMSWOOD CENTRE</div>
    <div class="line">18 Elmswood Street, Fairview 3071</div>
    <div class="contact-row"><span class="label">Phone:</span><span class="value">9555 0142</span></div>
    <div class="contact-row"><span class="label">Fax:</span><span class="value">9555 0143</span></div>
    <div class="contact-row"><span class="label">Email:</span><span class="value">qhco@mailbox.example</span></div>
  </address>

  <div class="sky-panel" role="img" aria-label="Pale blue sky with soft white clouds"></div>

  <h1 class="brand-name">Quiet Harbour Counselling</h1>
</main>
</body>
</html>
```